Luxury Real Estate Website, Midwest, United States

We need web design services for a luxury website. We need IDX Integration with our MLS. We want this to be a very simple website with amazing graphics. We want it to link up with our Postwren account in order to generate leads through a "More Information" Pop up on the main page. We want the main page to be covered with one large graphic that is a rolling slideshow of active listings of $400,000 and up from the IDX Integration. We need this website to give a very exclusive and sleek look. Lots of black is good... I will upload our logos in Black and Silver. We will also need an "About" page that we are going to call "Qeno Info". We want our graphics to be extremely impressive. Keep in mind, we are a company in the Midwest of the United States, and our real estate has a different look than homes in California or Florida. We need graphics that are realistic for the Midwest, yet still high-end.
Target Market(s)
Luxury Homeowners in the Midwest United States. The graphics needs to be pristine.
Industry/Entity Type
Real Estate
Coding
Coded - Design and coding required
Number of Pages Required
3 page
Requirements
Must have
- Large graphics with IDX Integration. The photos of real estate need to represent real estate that is common in the Midwest, United States. We also need Postwren integration. We need a pop up that is titled "My Free Market Analysis" that makes them fill out a contact form asking for Full Name, Email Address, Phone Number and Address. This needs to be a pop up on the front page and will integrate with our Postwren account. We also need a page called "About Qe No Home". And another page where clients can download informational PDFs. The main component needs to be a front page search engine connected with the IDX to access active listings from our MLS. I attached our logos and a sample front page of a website. I would love for ours to look similar.
Nice to have
- Lake House photos on midwest lakes are a plus.
Should not have
- Should not have clutter. This website needs to be clean, luxurious and exclusive.

```html
<!DOCTYPE html>
<html lang="en">
<head>
<meta charset="utf-8">
<title>Larkmoor Realty Group – Luxury Real Estate</title>
<link href="https://fonts.googleapis.com/css2?family=Montserrat:wght@400;500;600;700&family=Open+Sans:wght@400;600&display=swap" rel="stylesheet">
<style>
:root{
  --ink:#111214;
  --charcoal:#1c1d20;
  --graphite:#2a2b2f;
  --silver:#c9cacd;
  --mist:#8d8f94;
  --paper:#ffffff;
  --cloud:#f2f2f2;
  --line:#d9d9d9;
  --alert:#d7262b;
  --shade:rgba(8,9,11,.8);
}
*{box-sizing:border-box;margin:0;padding:0}
html,body{width:1200px;height:3468px;overflow:hidden;background:var(--paper)}
body{font-family:"Open Sans",Arial,sans-serif;color:var(--ink);position:relative}
.abs{position:absolute}
.heading{font-family:"Montserrat",Arial,sans-serif}

/* header + hero */
.hero{left:0;top:0;width:1200px;height:613px;
  background:linear-gradient(180deg,#3d5a7a 0%,#6f8aa6 30%,#5d6b4c 58%,#2e4a3d 72%,#5b6f7b 86%,#2b3a40 100%)}
.topbar{right:136px;top:22px;font:600 12px "Montserrat",sans-serif;color:var(--paper);display:flex;gap:28px;align-items:center}
.logo{left:132px;top:40px;display:flex;align-items:center;gap:12px;color:var(--paper);font:500 34px "Montserrat",sans-serif;letter-spacing:2px}
.logo .mark{width:14px;height:14px;background:var(--paper)}
.nav{left:580px;top:56px;display:flex;gap:40px;font:600 12px "Montserrat",sans-serif;color:var(--paper);letter-spacing:1px}
.nav .current{border-bottom:2px solid var(--paper);padding-bottom:4px}
.hero-title{left:169px;top:250px;font:700 44px/50px "Montserrat",sans-serif;color:var(--paper);letter-spacing:1px}
.search{left:169px;top:377px;width:437px;height:46px;display:flex}
.search .field{flex:1;background:var(--paper);font-size:13px;color:var(--mist);display:flex;align-items:center;justify-content:space-between;padding:0 18px}
.search .go{width:56px;background:var(--ink);display:flex;align-items:center;justify-content:center}
.dots{left:578px;top:538px;display:flex;gap:10px}
.dots span{width:9px;height:9px;border-radius:50%;background:var(--silver)}
.dots span.on{background:var(--paper)}

/* welcome */
.welcome-photo{left:132px;top:663px;width:312px;height:202px;background:linear-gradient(180deg,#8fa9c2,#6b6150 55%,#3f5233)}
.welcome-kicker{left:497px;top:682px;font:600 13px "Montserrat",sans-serif;letter-spacing:1px}
.welcome-name{left:497px;top:712px;font:500 32px/38px "Montserrat",sans-serif;text-transform:uppercase}
.welcome-rule{left:687px;top:680px;width:2px;height:170px;background:var(--line)}
.welcome-text{left:763px;top:684px;width:305px;font-size:12px;line-height:18px;color:#555}
.btn-dark{background:var(--ink);color:var(--paper);font:600 11px "Montserrat",sans-serif;letter-spacing:1px;display:flex;align-items:center;justify-content:center}
.welcome-btn{left:763px;top:790px;width:92px;height:26px}

/* featured */
.kicker{left:132px;top:985px;font:600 14px "Montserrat",sans-serif;letter-spacing:1px}
.featured-title{left:132px;top:1010px;font:700 28px "Montserrat",sans-serif;text-transform:uppercase}
.view-all{left:967px;top:1008px;width:101px;height:30px}
.card{top:1091px;width:220px}
.card .photo{height:158px}
.card .place{margin-top:24px;text-align:center;font-size:14px;color:#666}
.card .price{text-align:center;font:700 18px "Montserrat",sans-serif;margin-top:4px}

/* list grid */
.grid-intro{left:0;top:1383px;width:300px;height:237px;background:var(--charcoal);color:var(--paper);padding:88px 0 0 74px}
.grid-intro h3{font:700 20px "Montserrat",sans-serif;text-transform:uppercase}
.grid-intro p{font-size:11px;color:var(--mist);margin-top:10px;width:180px;line-height:16px}
.tile{width:300px;height:237px}
.tile .tag{position:absolute;right:10px;top:12px;background:var(--ink);color:var(--paper);font:600 11px "Montserrat",sans-serif;padding:5px 10px}
.tile .addr{position:absolute;left:20px;bottom:26px;color:var(--paper);font:700 13px "Montserrat",sans-serif;text-transform:uppercase}

/* blog */
.blog-title{left:0;top:1935px;width:1200px;text-align:center;font:700 20px "Montserrat",sans-serif;text-transform:uppercase}
.post{top:2030px;width:257px;height:375px;background:var(--cloud)}
.post .photo{height:169px}
.post h4{margin:24px 20px 0;font:700 12px/17px "Montserrat",sans-serif}
.post p{margin:12px 20px 0;font-size:11px;line-height:17px;color:#777}
.post .btn-dark{position:absolute;left:28px;top:318px;width:82px;height:24px;font-size:10px}

/* feature of the week */
.week{left:0;top:2513px;width:1200px;height:580px;background:linear-gradient(180deg,#b6c7d6 0%,#8f9aa0 35%,#5a6a4a 70%,#2d3a25 100%)}
.week-box{left:700px;top:2603px;width:345px;height:356px;background:rgba(17,18,20,.85);color:var(--paper);text-align:center;padding-top:56px}
.week-box h3{font:700 20px/28px "Montserrat",sans-serif;text-transform:uppercase}
.week-box p{font-size:12px;line-height:18px;color:var(--silver);margin:16px 50px 0}
.week-box .price{font:700 40px "Montserrat",sans-serif;margin-top:40px}
.week-box .btn-dark{width:112px;height:34px;margin:26px auto 0;background:var(--paper);color:var(--ink)}

/* footer */
.footer{left:0;top:3093px;width:1200px;height:375px;background:var(--paper)}
.foot-logo{left:132px;top:3192px;display:flex;align-items:center;gap:12px;font:500 38px "Montserrat",sans-serif;letter-spacing:2px}
.foot-logo .mark{width:14px;height:14px;background:var(--ink)}
.foot-col{top:3142px;font-size:12px;line-height:22px;color:#666}
.foot-col h5{font:700 12px "Montserrat",sans-serif;color:var(--ink);text-transform:uppercase;margin-bottom:16px}
.foot-row{display:flex;align-items:center;gap:10px;margin-bottom:12px}
.social-dot{width:26px;height:26px;border-radius:50%;background:var(--ink)}
.copyright{left:132px;top:3388px;font-size:11px;color:#777}
.partner{left:866px;top:3360px;display:flex;align-items:center;gap:10px;font:600 26px "Montserrat",sans-serif;color:var(--ink)}
.partner .mark{width:40px;height:40px;border-radius:50%;background:var(--graphite)}

/* popup */
.backdrop{left:0;top:0;width:1200px;height:3468px;background:var(--shade)}
.modal{left:386px;top:1168px;width:423px;height:560px;background:var(--paper);padding:64px 60px 0}
.modal h2{font:500 23px "Montserrat",sans-serif;color:var(--ink)}
.close{position:absolute;left:766px;top:1178px}
.modal .input{border:1px solid #bfbfbf;height:40px;margin-top:14px;font-size:11px;color:#333;padding:12px 16px}
.modal .input:first-of-type{margin-top:26px}
.modal .area{height:96px}
.modal .submit{margin-top:18px;height:53px;background:var(--charcoal);color:var(--paper);font:700 17px "Montserrat",sans-serif;display:flex;align-items:center;justify-content:center;letter-spacing:1px}
.modal .provider{margin-top:28px;display:flex;justify-content:center;align-items:center;gap:10px;font:600 22px "Montserrat",sans-serif;color:var(--ink)}
.modal .provider .mark{width:34px;height:34px;border-radius:50%;background:var(--graphite)}
</style>
</head>
<body>

<header>
  <div class="abs hero" role="img" aria-label="Lakeside Midwest luxury home at dusk reflected in the water"></div>
  <div class="abs topbar">
    <span>✉ info@larkmoor.com</span>
    <span style="display:flex;align-items:center;gap:6px">
      <svg width="12" height="12" viewBox="0 0 24 24"><path fill="#fff" d="M6.6 10.8a15.1 15.1 0 006.6 6.6l2.2-2.2c.3-.3.7-.4 1-.2 1.1.4 2.3.6 3.6.6.6 0 1 .4 1 1V20c0 .6-.4 1-1 1C10.6 21 3 13.4 3 4c0-.6.4-1 1-1h3.5c.6 0 1 .4 1 1 0 1.3.2 2.5.6 3.6.1.3 0 .7-.2 1z"/></svg>
      (312) 555-0148
    </span>
  </div>
  <div class="abs logo"><span class="mark"></span>LARKMOOR</div>
  <nav class="abs nav">
    <span class="current">HOME</span><span>LISTINGS</span><span>QENO INFO</span><span>RESOURCES</span><span>CONTACT</span>
  </nav>
  <h1 class="abs hero-title">LUXURY<br>REAL ESTATE</h1>
  <div class="abs search">
    <div class="field"><span>Enter city, zip or MLS number</span><span>Price ▾</span></div>
    <div class="go"><svg width="18" height="18" viewBox="0 0 24 24"><circle cx="10" cy="10" r="6.5" fill="none" stroke="#fff" stroke-width="2.4"/><path d="M15 15l5.5 5.5" stroke="#fff" stroke-width="2.6" stroke-linecap="round"/></svg></div>
  </div>
  <div class="abs dots"><span></span><span class="on"></span><span></span><span></span></div>
</header>

<section>
  <div class="abs welcome-photo" role="img" aria-label="Large brick family estate with manicured lawn"></div>
  <p class="abs welcome-kicker">WELCOME TO</p>
  <h2 class="abs welcome-name">Larkmoor<br>Realty<br>Group</h2>
  <div class="abs welcome-rule"></div>
  <p class="abs welcome-text">We represent the finest homes across the Midwest, from quiet lakefront retreats to grand estates on rolling land. Our team pairs deep local insight with discreet, personal service for every client we serve.</p>
  <div class="abs btn-dark welcome-btn">READ MORE</div>
</section>

<section>
  <p class="abs kicker">FEATURED</p>
  <h2 class="abs featured-title">Luxury Homes</h2>
  <div class="abs btn-dark view-all">VIEW MORE</div>
  <article class="abs card" style="left:132px"><div class="photo" role="img" aria-label="Stone manor with front lawn" style="background:linear-gradient(180deg,#9fb4c8,#7a7568 60%,#4f6a3a)"></div><p class="place">Lake Geneva, WI</p><p class="price">$2,350,000</p></article>
  <article class="abs card" style="left:372px"><div class="photo" role="img" aria-label="Colonial home among autumn trees" style="background:linear-gradient(180deg,#8fa6bb,#8a5c3e 55%,#50663a)"></div><p class="place">Carmel, IN</p><p class="price">$2,350,000</p></article>
  <article class="abs card" style="left:610px"><div class="photo" role="img" aria-label="Brick estate at golden hour" style="background:linear-gradient(180deg,#c2a078,#7d4b34 55%,#455a33)"></div><p class="place">Edina, MN</p><p class="price">$2,350,000</p></article>
  <article class="abs card" style="left:848px"><div class="photo" role="img" aria-label="Dark timber lake house at evening" style="background:linear-gradient(180deg,#5b6878,#3b3530 55%,#2f3d2b)"></div><p class="place">Lake Ozark, MO</p><p class="price">$2,350,000</p></article>
</section>

<section>
  <div class="abs grid-intro"><h3>List of Homes</h3><p>Browse active listings from $400,000 across the region.</p></div>
  <div class="abs tile" style="left:300px;top:1383px;background:linear-gradient(180deg,#8ea2b5,#7b4a3a 55%,#3e5230)" role="img" aria-label="Red brick home with gables"><span class="tag">$1,280,000</span><span class="addr">1200 Birch Lane</span></div>
  <div class="abs tile" style="left:600px;top:1383px;background:linear-gradient(180deg,#9bb0c3,#6f6a62 55%,#4a6237)" role="img" aria-label="Stone house with large lawn"><span class="tag">$1,280,000</span><span class="addr">48 Harbor Road</span></div>
  <div class="abs tile" style="left:900px;top:1383px;background:linear-gradient(180deg,#a9bccc,#5e6b77 55%,#476034)" role="img" aria-label="Blue-grey farmhouse in green yard"><span class="tag">$1,280,000</span><span class="addr">905 Maple Ridge</span></div>
  <div class="abs tile" style="left:0;top:1620px;background:linear-gradient(180deg,#a6b8c8,#8a7a66 55%,#3f5a6a)" role="img" aria-label="Waterfront home with dock"><span class="tag">$1,280,000</span><span class="addr">22 Shore Drive</span></div>
  <div class="abs tile" style="left:300px;top:1620px;background:linear-gradient(180deg,#95a8ba,#6b5141 55%,#485e33)" role="img" aria-label="Two-storey brick colonial"><span class="tag">$1,280,000</span><span class="addr">310 Oak Court</span></div>
  <div class="abs tile" style="left:600px;top:1620px;background:linear-gradient(180deg,#b3c3d0,#7c7d7a 55%,#51663c)" role="img" aria-label="White home with covered porch"><span class="tag">$1,280,000</span><span class="addr">77 Elm Street</span></div>
  <div class="abs tile" style="left:900px;top:1620px;background:linear-gradient(180deg,#9fb3c6,#7a5744 55%,#4b6236)" role="img" aria-label="Brick manor with tall chimneys"><span class="tag">$1,280,000</span><span class="addr">560 Cedar Way</span></div>
</section>

<section>
  <h2 class="abs blog-title">From Our Blog</h2>
  <article class="abs post" style="left:178px"><div class="photo" role="img" aria-label="Stone manor under blue sky" style="background:linear-gradient(180deg,#9bb2c7,#6e6658 60%,#4c6438)"></div><h4>Preparing your lakefront home for a spring sale this year</h4><p>Simple steps to help your property stand out to serious buyers across the region.</p><div class="btn-dark">READ MORE</div></article>
  <article class="abs post" style="left:472px"><div class="photo" role="img" aria-label="Country home on a green lawn" style="background:linear-gradient(180deg,#a9bccd,#7e7a6c 55%,#4e6a37)"></div><h4>What buyers look for in a modern Midwest estate today</h4><p>From open kitchens to quiet acreage, the features that matter most right now.</p><div class="btn-dark">READ MORE</div></article>
  <article class="abs post" style="left:768px"><div class="photo" role="img" aria-label="White colonial with tall trees" style="background:linear-gradient(180deg,#b6c6d3,#878a88 55%,#506a3c)"></div><h4>Understanding market value before you list your home</h4><p>How a free market analysis helps you price with confidence and sell sooner.</p><div class="btn-dark">READ MORE</div></article>
</section>

<section>
  <div class="abs week" role="img" aria-label="Large grey shingle estate with landscaped garden"></div>
  <div class="abs week-box">
    <h3>Luxury Real Estate<br>of the Week</h3>
    <p>A refined lakeside residence with private dock, wooded views and five spacious bedrooms.</p>
    <div class="price">$1,225,00</div>
    <div class="btn-dark">READ MORE</div>
  </div>
</section>

<footer>
  <div class="abs footer"></div>
  <div class="abs foot-logo"><span class="mark"></span>LARKMOOR</div>
  <div class="abs foot-col" style="left:500px">
    <h5>Contact Us</h5>
    <div class="foot-row"><svg width="12" height="14" viewBox="0 0 24 28"><path d="M12 0a9 9 0 019 9c0 7-9 19-9 19S3 16 3 9a9 9 0 019-9z" fill="#111"/><circle cx="12" cy="9" r="3.5" fill="#fff"/></svg><span>410 Lakeview Ave<br>Madison, WI 53703</span></div>
    <div class="foot-row"><svg width="12" height="12" viewBox="0 0 24 24"><path fill="#111" d="M6.6 10.8a15.1 15.1 0 006.6 6.6l2.2-2.2c.3-.3.7-.4 1-.2 1.1.4 2.3.6 3.6.6.6 0 1 .4 1 1V20c0 .6-.4 1-1 1C10.6 21 3 13.4 3 4c0-.6.4-1 1-1h3.5c.6 0 1 .4 1 1 0 1.3.2 2.5.6 3.6.1.3 0 .7-.2 1z"/></svg><span>(312) 555-0148</span></div>
    <div class="foot-row"><svg width="13" height="10" viewBox="0 0 26 20"><rect width="26" height="20" fill="#111"/><path d="M1 1l12 10L25 1" fill="none" stroke="#fff" stroke-width="2"/></svg><span>info@larkmoor.com</span></div>
  </div>
  <div class="abs foot-col" style="left:747px">
    <h5>Menu</h5>
    <div>Home</div><div>Listings</div><div>Qeno Info</div><div>Resources</div><div>Contact</div>
  </div>
  <div class="abs foot-col" style="left:934px">
    <h5>Connect With Us</h5>
    <div class="foot-row"><span class="social-dot"></span><span>Updates</span></div>
    <div class="foot-row"><span class="social-dot"></span><span>Journal</span></div>
    <div class="foot-row"><span class="social-dot"></span><span>Network</span></div>
  </div>
  <p class="abs copyright">Copyright © 2024. All Rights Reserved.</p>
  <div class="abs partner"><span class="mark"></span>Postwren</div>
</footer>

<div class="abs backdrop"></div>
<div class="abs modal" role="dialog" aria-label="My Free Market Analysis">
  <h2>My Free Market Analysis</h2>
  <div class="input">Full Name</div>
  <div class="input">Email Address</div>
  <div class="input">Phone Number</div>
  <div class="input area">Address</div>
  <div class="submit">SUBMIT</div>
  <div class="provider"><span class="mark"></span>Postwren</div>
</div>
<svg class="close" width="36" height="36" viewBox="0 0 36 36" aria-label="Close">
  <circle cx="18" cy="18" r="16" fill="var(--alert)" stroke="#fff" stroke-width="2"/>
  <path d="M12 12l12 12M24 12L12 24" stroke="#fff" stroke-width="4" stroke-linecap="round"/>
</svg>

</body>
</html>
```